Home Remodeling company needs a business card design

we need a business card design for home remodeling company in hamilton county, indiana USA. we offers a wide range of construction services including whole house renovations, Design and Build Basements and Kitchen and Bathroom Remodeling . we would like to see designs for both site of business card that use the same color of the company logo and also including all information below :
1- Karim Feltous CEO / General Contractor
2- all company contacts Telephone numbers ( 1-888-DULOM-47 ) ( 317-555-0193) email address ( info@dulomhome.com) website ( www.dulomhome.com ) and social media logos (Facebook- twitter- google plus )
3- company logo
4- licensed . insured . bonded

```html
<!DOCTYPE html>
<html lang="en">
<head>
<meta charset="utf-8">
<title>DULOM Home Remodeling – Business Card</title>
<link href="https://fonts.googleapis.com/css2?family=Open+Sans:wght@400;600;800&display=swap" rel="stylesheet">
<style>
  :root {
    --brand-red: #c8303a;
    --charcoal: #3a3a3c;
    --tag-grey: #77777a;
    --band-grey: #a9a7a8;
    --paper: #ffffff;
    --backdrop: #e9e7e4;
    --social-a: #d7442f;
    --social-b: #3c5ea6;
    --social-c: #1eaee8;
  }
  * { box-sizing: border-box; margin: 0; padding: 0; }
  html, body {
    width: 1189px; height: 1200px; overflow: hidden;
    background: var(--backdrop);
    font-family: "Open Sans", Arial, sans-serif;
  }
  .card {
    position: absolute; left: 140px;
    width: 917px; height: 524px;
    overflow: hidden;
    box-shadow: 0 4px 12px rgba(0,0,0,.25);
  }
  .card--front { top: 45px; background: var(--paper); }
  .card--back { top: 624px; background: var(--brand-red); }
  .wave { position: absolute; inset: 0; width: 100%; height: 100%; }

  .wordmark {
    position: absolute; left: 75px; top: 18px;
    font-weight: 800; font-size: 108px; line-height: 1;
    letter-spacing: 6px; color: var(--charcoal);
  }
  .tagline {
    position: absolute; left: 78px; top: 133px;
    font-weight: 600; font-size: 29px; line-height: 1;
    letter-spacing: 15.5px; color: var(--tag-grey);
  }

  .person { position: absolute; right: 47px; top: 208px; text-align: right; color: var(--paper); }
  .person__name { font-size: 38px; font-weight: 600; line-height: 1.2; }
  .person__title { font-size: 28px; line-height: 1.3; }

  .contacts { position: absolute; right: 52px; top: 338px; list-style: none; }
  .contacts li {
    display: flex; justify-content: flex-end; align-items: center;
    height: 39px; font-size: 27px; color: var(--paper);
  }
  .contacts svg { width: 21px; height: 21px; margin-left: 30px; flex: none; }

  .social { position: absolute; left: 43px; top: 422px; display: flex; gap: 18px; }
  .social span { width: 66px; height: 64px; border-radius: 8px; }
  .social .a { background: var(--social-a); }
  .social .b { background: var(--social-b); }
  .social .c { background: var(--social-c); }

  .back-lockup {
    position: absolute; left: 0; right: 0; top: 176px; text-align: center;
  }
  .back-lockup .wordmark {
    position: static; display: block; font-size: 122px; letter-spacing: 10px;
  }
  .back-lockup .tagline {
    position: static; display: block; margin-top: 6px;
    font-size: 34px; letter-spacing: 19px; color: #8a8888;
  }
</style>
</head>
<body>
  <section class="card card--front">
    <svg class="wave" viewBox="0 0 917 524" preserveAspectRatio="none" aria-hidden="true">
      <path d="M0,318 C280,292 440,270 590,188 C710,120 830,96 917,95 L917,524 L0,524 Z" fill="var(--band-grey)"/>
      <path d="M0,371 C300,334 450,302 610,206 C725,138 830,108 917,104 L917,524 L0,524 Z" fill="var(--brand-red)" stroke="var(--paper)" stroke-width="3"/>
    </svg>

    <div class="wordmark">DULOM</div>
    <div class="tagline">HOME REMODELING</div>

    <div class="person">
      <p class="person__name">Karim Feltous</p>
      <p class="person__title">CEO / General Contractor</p>
    </div>

    <ul class="contacts">
      <li>1-888-DULOM-47
        <svg viewBox="0 0 20 20"><rect width="20" height="20" fill="#fff"/><path d="M6 4 L9 4 L9 7 L8 8 Q9 11 12 12 L13 11 L16 11 L16 14 Q15 16 12 15 Q6 13 5 7 Q5 5 6 4Z" fill="var(--brand-red)"/></svg>
      </li>
      <li>317-555-0193
        <svg viewBox="0 0 20 20"><rect width="20" height="20" fill="#fff"/><path d="M6 4 L9 4 L9 7 L8 8 Q9 11 12 12 L13 11 L16 11 L16 14 Q15 16 12 15 Q6 13 5 7 Q5 5 6 4Z" fill="var(--brand-red)"/></svg>
      </li>
      <li>info@dulomhome.com
        <svg viewBox="0 0 20 20"><rect width="20" height="20" fill="#fff"/><rect x="3" y="5" width="14" height="10" fill="var(--brand-red)"/><path d="M3 5 L10 11 L17 5" fill="none" stroke="#fff" stroke-width="1.5"/></svg>
      </li>
      <li>www.dulomhome.com
        <svg viewBox="0 0 20 20"><rect width="20" height="20" fill="#fff"/><circle cx="10" cy="10" r="6.5" fill="var(--brand-red)"/><path d="M3.5 10 H16.5 M10 3.5 V16.5" stroke="#fff" stroke-width="1.2"/></svg>
      </li>
    </ul>

    <div class="social" aria-label="Social media links">
      <span class="a"></span><span class="b"></span><span class="c"></span>
    </div>
  </section>

  <section class="card card--back">
    <div class="back-lockup">
      <span class="wordmark">DULOM</span>
      <span class="tagline">HOME REMODELING</span>
    </div>
  </section>
</body>
</html>
```